brightwell - Property Management DL Card

I am after a savvy designer to cut through junk mail! so many real estate agents use flyers to promote themselves and their business and usually sales. We are a property management firm (residential) and we want to represent landlords that have existing investment properties and need a quality agent to represent them. Can you help?
DL size, will be printed and delivered to mailboxes. For a look at our website go to www.brightwellrs.com.au. Keep it simple and clutter free.
it is to be double sided - with one side to be simple and clear - just our website, logo and telephone number on the back.
attached is our logo and our telephone number is 1300 48 92 16
the above are 2 essential elements to be included + our email address: admin@brightwellrs.com.au
also attached are our transparent price list

Target Market(s)
property investors,
people that manage properties themselves
Industry/Entity Type
Property Management
- arial
Look and feel

```html
<!DOCTYPE html>
<html lang="en">
<head>
<meta charset="utf-8">
<title>brightwell – Property Management DL Card</title>
<link href="https://fonts.googleapis.com/css2?family=Open+Sans:wght@300;400;600&display=swap" rel="stylesheet">
<style>
  :root {
    --canvas-bg: #e4e4e4;
    --beige: #e3d9b6;
    --black: #050505;
    --rust: #c4402a;
    --rust-text: #f3c9bb;
    --white: #ffffff;
    --phone-red: #d4412c;
    --divider: #f0d6cc;
    --photo-dark: #3a2c26;
    --photo-mid: #7a6253;
    --photo-light: #e6d8c6;
  }
  * { margin: 0; padding: 0; box-sizing: border-box; }
  html, body {
    width: 1200px; height: 1200px; overflow: hidden;
    background: var(--canvas-bg);
    font-family: "Open Sans", Arial, sans-serif;
  }
  .canvas { position: relative; width: 1200px; height: 1200px; }

  /* Front of card */
  .card-front {
    position: absolute; left: 121px; top: 59px;
    width: 996px; height: 497px;
    background: var(--black);
  }
  .front-band-top {
    position: absolute; left: 0; top: 0; width: 100%; height: 65px;
    background: var(--beige);
  }
  .front-photo {
    position: absolute; left: 0; top: 65px; width: 715px; height: 359px;
    background:
      linear-gradient(90deg, var(--photo-dark) 0%, var(--photo-mid) 30%, var(--photo-light) 55%, var(--photo-mid) 80%, #cfc6bc 100%);
  }
  .front-photo::after {
    content: ""; position: absolute; inset: 0;
    background: linear-gradient(180deg, rgba(255,255,255,0.18) 0%, rgba(0,0,0,0) 40%, rgba(40,28,24,0.35) 100%);
  }
  .front-brand {
    position: absolute; left: 715px; top: 65px; width: 281px; height: 359px;
    display: flex; align-items: center; justify-content: center;
  }
  .brand-name {
    font-weight: 300; color: var(--white); letter-spacing: 0.5px; line-height: 1;
  }
  .front-brand .brand-name { font-size: 40px; margin-top: -10px; }

  .front-band-bottom {
    position: absolute; left: 0; top: 424px; width: 100%; height: 73px;
    background: var(--rust);
    color: var(--white);
  }
  .front-tagline {
    position: absolute; left: 52px; top: 22px;
    font-size: 21px; font-weight: 600; color: var(--rust-text);
  }
  .front-divider {
    position: absolute; left: 421px; top: 17px; width: 1px; height: 38px;
    background: var(--divider);
  }
  .benefit-list {
    position: absolute; top: 15px; list-style: none;
    font-size: 16px; line-height: 21px;
  }
  .benefit-list li::before { content: "•"; margin-right: 6px; }
  .benefit-list--first { left: 446px; }
  .benefit-list--second { left: 711px; }

  /* Back of card */
  .card-back {
    position: absolute; left: 119px; top: 637px;
    width: 1000px; height: 500px;
    background: #000;
  }
  .back-brand { position: absolute; left: 54px; top: 48px; }
  .back-brand .brand-name { font-size: 44px; }
  .contact-block {
    position: absolute; left: 558px; top: 381px;
    border-left: 2px solid #9a9a9a;
    padding-left: 20px;
    font-size: 17px; line-height: 24.5px; letter-spacing: 0.5px;
    color: var(--white);
  }
  .contact-phone { color: var(--phone-red); }
</style>
</head>
<body>
<main class="canvas">
  <section class="card-front">
    <div class="front-band-top"></div>
    <div class="front-photo" role="img" aria-label="Photograph of a modern apartment interior with lounge, kitchen bar and staircase"></div>
    <div class="front-brand"><span class="brand-name">brightwell</span></div>
    <div class="front-band-bottom">
      <p class="front-tagline">Property Management specialists</p>
      <span class="front-divider"></span>
      <ul class="benefit-list benefit-list--first">
        <li>Excellent communication</li>
        <li>Minimal vacancy</li>
      </ul>
      <ul class="benefit-list benefit-list--second">
        <li>No hidden extras</li>
        <li>The best rent return</li>
      </ul>
    </div>
  </section>

  <section class="card-back">
    <div class="back-brand"><span class="brand-name">brightwell</span></div>
    <address class="contact-block" style="font-style:normal">
      <div class="contact-phone">1300 48 92 16</div>
      <div class="contact-address">PO Box B527, Harbourview NSW, 2199</div>
      <div class="contact-email">admin@brightwellrs.com.au</div>
    </address>
  </section>
</main>
</body>
</html>
```